Note Cards for Clients

Hi - I need a design for simple flat note-cards and envelopes to use to send clients a written note in a professional manner. Please use my logo and color scheme.

Hi again- sorry for the miscommunication. I'd like to have note-cards 5x8 with envelopes as opposed to traditional stationary samples.

Thanks!

It Professional

```html
<!DOCTYPE html>
<html lang="en">
<head>
<meta charset="UTF-8">
<title>Ridgeline Wealth Partners – Note Card</title>
<link rel="stylesheet" href="https://fonts.googleapis.com/css2?family=Cormorant+Garamond:wght@600&display=swap">
<style>
  :root {
    --paper: #ffffff;
    --card-edge: #000000;
    --frame: #5b5d60;
    --brand-blue: #1c3fa0;
  }
  html, body {
    margin: 0;
    padding: 0;
    overflow: hidden;
    background: var(--paper);
  }
  .note-card {
    position: relative;
    width: 1200px;
    height: 813px;
    box-sizing: border-box;
    border: 1px solid var(--card-edge);
    background: var(--paper);
    overflow: hidden;
  }
  .writing-frame {
    position: absolute;
    left: 45px;
    top: 43px;
    width: 1110px;
    height: 728px;
    box-sizing: border-box;
    border: 2px solid var(--frame);
    border-radius: 13px;
  }
  .brand-plate {
    position: absolute;
    left: 38px;
    top: 34px;
    width: 372px;
    height: 106px;
    background: var(--paper);
    display: flex;
    align-items: center;
    gap: 16px;
    padding-left: 10px;
    box-sizing: border-box;
  }
  .brand-square {
    width: 62px;
    height: 62px;
    background: var(--brand-blue);
    flex: none;
  }
  .brand-name {
    font-family: "Cormorant Garamond", Georgia, serif;
    font-weight: 600;
    font-size: 31px;
    line-height: 1.05;
    letter-spacing: 0.04em;
    text-transform: uppercase;
    color: var(--brand-blue);
    margin: 0;
  }
</style>
</head>
<body>
  <main class="note-card">
    <div class="writing-frame"></div>
    <header class="brand-plate">
      <span class="brand-square" aria-hidden="true"></span>
      <p class="brand-name">Ridgeline<br>Wealth Partners</p>
    </header>
  </main>
</body>
</html>
```